Executive Business Card for Healthcare Company [Need Today]

I need a business card design for a healthcare company. The only branding the company has thus far is a logo. The cards will be utilized by company executives. The design I envision will be vibrant and appealing but with a corporate feel. They shouldn't be too casual or playful. I would like to complete this project TODAY if possible.

Target Market(s)

Healthcare vendors, other executives in healthcare and pharmaceuticals

Industry/Entity Type

Pharmaceutical

Contact Information for Business Card

See attachment

Font styles to use
Serif
Sans Serif

Colors

Designer to choose colors to be used in the design.

```html
<!DOCTYPE html>
<html lang="en">
<head>
<meta charset="utf-8">
<title>Corvane Therapeutics – Business Card</title>
<link href="https://fonts.googleapis.com/css2?family=Open+Sans:wght@400;600;700&display=swap" rel="stylesheet">
<style>
  :root {
    --teal: #36bfc6;
    --teal-deep: #2fb3ba;
    --green: #46a874;
    --green-dark: #2e8b57;
    --ink: #1e1e1e;
    --paper: #ffffff;
    --backdrop: #e9ecee;
  }
  html, body {
    margin: 0;
    padding: 0;
    width: 1200px;
    height: 1000px;
    overflow: hidden;
    background: var(--backdrop);
    font-family: "Open Sans", Arial, sans-serif;
  }
  .canvas {
    position: relative;
    width: 1200px;
    height: 1000px;
  }
  .card {
    position: absolute;
    left: 250px;
    width: 700px;
    height: 400px;
    border-radius: 26px;
    overflow: hidden;
    box-shadow: 0 8px 24px rgba(0,0,0,0.18);
  }
  .card--front { top: 60px; background: var(--teal); }
  .card--back  { top: 540px; background: var(--paper); }

  /* brand lockup */
  .brand {
    position: absolute;
    display: flex;
    align-items: center;
    gap: 18px;
  }
  .brand__dot {
    border-radius: 50%;
    flex: none;
  }
  .brand__name {
    font-weight: 400;
    line-height: 1.05;
    letter-spacing: 0.5px;
  }
  .card--front .brand { left: 150px; top: 130px; }
  .card--front .brand__dot { width: 130px; height: 130px; border: 3px solid var(--paper); }
  .card--front .brand__name { color: var(--paper); font-size: 48px; }

  .card--back .brand { right: 40px; top: 28px; gap: 14px; }
  .card--back .brand__dot { width: 88px; height: 88px; border: 2px solid var(--green); }
  .card--back .brand__name { color: var(--teal-deep); font-size: 30px; }

  .waves { position: absolute; inset: 0; }

  .person {
    position: absolute;
    left: 50px;
    top: 160px;
  }
  .person__name {
    margin: 0;
    color: var(--green-dark);
    font-size: 24px;
    font-weight: 700;
    letter-spacing: 0.5px;
  }
  .person__title {
    margin: 2px 0 0;
    color: var(--ink);
    font-size: 15px;
  }
  .address {
    position: absolute;
    left: 50px;
    top: 262px;
    margin: 0;
    font-style: normal;
    color: var(--ink);
    font-size: 16px;
    font-weight: 600;
    line-height: 1.3;
  }
  .contact {
    position: absolute;
    right: 34px;
    top: 262px;
    margin: 0;
    padding: 0;
    list-style: none;
    color: var(--paper);
    font-size: 15px;
    line-height: 1.55;
    text-align: right;
  }
  .contact li { display: flex; align-items: center; justify-content: flex-end; gap: 7px; }
  .contact svg { width: 13px; height: 13px; flex: none; }
</style>
</head>
<body>
<main class="canvas">

  <section class="card card--front" aria-label="Card front">
    <div class="brand">
      <span class="brand__dot"></span>
      <span class="brand__name">corvane<br>therapeutics</span>
    </div>
  </section>

  <section class="card card--back" aria-label="Card back">
    <svg class="waves" viewBox="0 0 700 400" width="700" height="400" aria-hidden="true">
      <path fill="var(--green)" d="M700 120 C600 150 520 220 450 280 C380 340 290 385 160 400 L700 400 Z"/>
      <path fill="var(--paper)" d="M640 128 C560 170 500 240 450 300 C410 348 360 380 300 398 C370 372 420 338 462 290 C520 222 580 160 640 128 Z"/>
      <path fill="var(--teal)" d="M0 372 C170 355 360 330 505 250 C420 330 250 372 0 392 Z"/>
    </svg>

    <div class="brand">
      <span class="brand__dot"></span>
      <span class="brand__name">corvane<br>therapeutics</span>
    </div>

    <div class="person">
      <h1 class="person__name">MARTIN HALE</h1>
      <p class="person__title">Senior Director of Marketing</p>
    </div>

    <address class="address">
      Corvane Therapeutics, LLC<br>
      118 N Lumpkin Avenue<br>
      Riverton, GA 30699
    </address>

    <ul class="contact">
      <li>
        <svg viewBox="0 0 16 16" aria-hidden="true"><path fill="currentColor" d="M3.5 1.5l2.5 0 1 3.5-1.7 1.2c.8 1.8 2.2 3.2 4 4l1.2-1.7 3.5 1v2.5c0 .8-.7 1.5-1.5 1.5C6.8 13.5 2 8.7 2 3c0-.8.7-1.5 1.5-1.5z"/></svg>
        555-204-7710 (Office)
      </li>
      <li>555-318-6642 (Cell)</li>
      <li>
        <svg viewBox="0 0 16 16" aria-hidden="true"><rect x="1.5" y="3.5" width="13" height="9" rx="1.2" fill="none" stroke="currentColor" stroke-width="1.5"/><path d="M2 4.5l6 4.5 6-4.5" fill="none" stroke="currentColor" stroke-width="1.5"/></svg>
        mhale@corvanerx.com
      </li>
    </ul>
  </section>

</main>
</body>
</html>
```